Looking for a modern, Professional business card design

We have a simple business card, but are looking for a more modern, professional look. A sample of the basic card is attached as well as the logo. We would also like to add that we offer:
Struggling with your finances?
- Learn to become debt free
- Discover the power of cash
- Control your money instead of it controlling you
Let us help you achieve a new level of financial freedom!
Also, we would like to have a "SPECIAL OFFER!: FREE 30 minute consultation"
Financial Planning

```html
<!DOCTYPE html>
<html lang="en">
<head>
<meta charset="utf-8">
<title>Summit Money Coaching – Business Card</title>
<link href="https://fonts.googleapis.com/css2?family=Open+Sans:wght@400;600;700&display=swap" rel="stylesheet">
<style>
  :root {
    --backdrop: #3a3633;
    --card: #0b0b0b;
    --green: #6cc93a;
    --green-deep: #3f9a1f;
    --white: #f4f4f4;
  }
  * { margin: 0; padding: 0; box-sizing: border-box; }
  html, body {
    width: 1200px; height: 844px; overflow: hidden;
    background: var(--backdrop);
    font-family: "Open Sans", Arial, sans-serif;
  }
  .stage {
    position: relative; width: 1200px; height: 844px;
    display: flex; align-items: center; justify-content: center; gap: 40px;
  }
  .card {
    position: relative; width: 540px; height: 309px;
    background: var(--card);
    border-radius: 3px;
    box-shadow: 0 10px 30px rgba(0,0,0,.45);
    color: var(--white);
  }
  .brand {
    display: flex; align-items: center; gap: 10px;
  }
  .brand-dot {
    width: 18px; height: 18px; border-radius: 50%;
    background: var(--green); flex: none;
  }
  .brand-name {
    font-weight: 700; color: var(--green);
    text-transform: uppercase; letter-spacing: .5px; line-height: 1.1;
  }

  /* Front */
  .front .brand { position: absolute; left: 150px; top: 78px; }
  .front .brand-name { font-size: 26px; }
  .holder { position: absolute; left: 32px; bottom: 40px; }
  .holder-name { color: var(--green); font-size: 21px; font-weight: 600; line-height: 1.2; }
  .holder-title { font-size: 15px; line-height: 1.3; }
  .contact {
    position: absolute; right: 30px; bottom: 40px;
    list-style: none; text-align: right; font-size: 14px; line-height: 1.55;
  }
  .contact li { display: flex; justify-content: flex-end; align-items: center; gap: 6px; }
  .contact svg { width: 12px; height: 12px; flex: none; }
  .contact .plain { padding-right: 18px; }

  /* Back */
  .back { text-align: center; padding-top: 34px; }
  .back .brand { justify-content: center; margin-bottom: 20px; }
  .back .brand-name { font-size: 20px; }
  .pitch-heading { color: var(--green); font-size: 15px; font-weight: 600; margin-bottom: 4px; }
  .benefits { list-style: none; font-size: 14px; line-height: 1.45; }
  .benefits li:last-child { margin-top: 6px; }
  .promise { color: var(--green); font-size: 14px; font-weight: 600; margin-top: 12px; }
  .offer { font-size: 15px; margin-top: 8px; color: var(--green); font-weight: 600; }
  .offer span { color: var(--white); font-size: 14px; }
</style>
</head>
<body>
<main class="stage">
  <section class="card front" aria-label="Card front">
    <div class="brand">
      <span class="brand-dot"></span>
      <span class="brand-name">Summit Money<br>Coaching</span>
    </div>
    <div class="holder">
      <p class="holder-name">Daniel R. Hale</p>
      <p class="holder-title">Personal Financial Coach</p>
    </div>
    <ul class="contact">
      <li>(555) 014-2280
        <svg viewBox="0 0 12 12" aria-hidden="true"><path fill="var(--green)" d="M2.5 1l2 2.2-1 1.3c.6 1.5 1.8 2.7 3.3 3.3l1.3-1 2.2 2-.9 1.6C5.5 10.2 1.8 6.5 1 2z"/></svg>
      </li>
      <li>daniel@steadymoneypath.com
        <svg viewBox="0 0 12 12" aria-hidden="true"><rect x="1" y="2.5" width="10" height="7" rx="1" fill="var(--green)"/><path d="M1.5 3l4.5 3.5L10.5 3" stroke="var(--card)" fill="none" stroke-width="1"/></svg>
      </li>
      <li>www.steadymoneypath.com
        <svg viewBox="0 0 12 12" aria-hidden="true"><circle cx="6" cy="6" r="5" fill="var(--green)"/><path d="M1 6h10M6 1c-2.5 2.8-2.5 7.2 0 10M6 1c2.5 2.8 2.5 7.2 0 10" stroke="var(--card)" fill="none" stroke-width=".8"/></svg>
      </li>
    </ul>
  </section>

  <section class="card back" aria-label="Card back">
    <div class="brand">
      <span class="brand-dot"></span>
      <span class="brand-name">Summit Money Coaching</span>
    </div>
    <p class="pitch-heading">Struggling with your finances?</p>
    <ul class="benefits">
      <li>Learn to become debt free</li>
      <li>Discover the power of cash</li>
      <li>Control your money instead of it controlling you</li>
    </ul>
    <p class="promise">Let us help you achieve a new level of financial freedom!</p>
    <p class="offer">SPECIAL OFFER!: <span>FREE 30 minute consultation</span></p>
  </section>
</main>
</body>
</html>
```